New Innovative Counselling and psychotherapy Service needs Business Card design

Keep it simple and professional. On one side, just company name and logo (perhaps in all blue) and maybe a tag line.

On other side (all white) my name and Qualifications in centre

Industry/Entity Type

Health And Wellness

Contact Information for Business Card

Dara Whelby
Counsellor & Psychotherapist
BSc (Psychol.), BA, Dip. (Couns. & Psych.), PG.Cert (CBT), FGTrK, ONRE

I will also require Mobile no, Email and web site address of which I'll pass on to final designer.

Font styles to use
Sans Serif

Requirements
Must have
• My Logo Only and please use the colours in logo that is in it.
Should not have
• Any other images

```html
<!DOCTYPE html>
<html lang="en">
<head>
<meta charset="utf-8">
<title>Kindle Grove – Business Card</title>
<link href="https://fonts.googleapis.com/css2?family=Roboto:wght@400;500&family=Roboto+Condensed:wght@400;700&display=swap" rel="stylesheet">
<style>
  :root{
    --stage:#2f2f2f;
    --card-dark:#353535;
    --card-light:#f1f1f1;
    --brand-blue:#45b3ea;
    --brand-green:#97d35c;
    --ink:#444444;
    --white:#ffffff;
  }
  *{box-sizing:border-box;margin:0;padding:0}
  html,body{width:1200px;height:960px;overflow:hidden}
  body{background:var(--stage);position:relative;font-family:"Roboto",Arial,sans-serif}
  .card{position:absolute;width:600px;height:342px;box-shadow:0 3px 8px rgba(0,0,0,.5);overflow:hidden}
  .card-front{left:322px;top:110px;background:var(--card-dark)}
  .card-back{left:320px;top:493px;background:var(--brand-blue)}
  .front-swoosh{position:absolute;inset:0}
  .identity{position:absolute;left:21px;top:94px}
  .person-name{font-family:"Roboto Condensed",Arial,sans-serif;font-size:21px;font-weight:400;color:var(--brand-blue);line-height:1.1}
  .person-role{font-family:"Roboto Condensed",Arial,sans-serif;font-size:14.5px;font-weight:700;color:var(--brand-green);margin-top:3px}
  .person-quals{font-family:"Roboto Condensed",Arial,sans-serif;font-size:11px;color:var(--brand-green);line-height:1.3;margin-top:2px}
  .contact-list{list-style:none;margin-top:17px}
  .contact-list li{display:flex;align-items:center;gap:8px;color:var(--white);font-size:14px;line-height:19px}
  .contact-list svg{width:13px;height:13px;flex:none}
  .brand-lockup{position:absolute;left:333px;top:152px;display:flex;align-items:center;gap:12px}
  .brand-dot{width:36px;height:36px;border-radius:50%;background:var(--brand-blue)}
  .brand-name{font-size:23px;font-weight:400;color:var(--ink)}
  .back-name{position:absolute;left:0;right:0;top:128px;text-align:center;font-size:44px;font-weight:500;color:var(--white)}
  .tagline{position:absolute;left:0;right:0;top:288px;text-align:center;font-size:14.5px;color:var(--white)}
</style>
</head>
<body>
  <section class="card card-front">
    <svg class="front-swoosh" viewBox="0 0 600 342" width="600" height="342">
      <path d="M362 0 C262 70 255 255 376 342 L600 342 L600 0Z" fill="var(--brand-green)"/>
      <path d="M378 0 C282 58 268 238 370 342 L600 342 L600 0Z" fill="var(--brand-blue)"/>
      <path d="M388 0 C296 66 286 250 378 342 L600 342 L600 0Z" fill="var(--card-light)" stroke="var(--white)" stroke-width="3"/>
    </svg>
    <div class="identity">
      <h1 class="person-name">DARA WHELBY</h1>
      <p class="person-role">COUNSELLOR &amp; PSYCHOTHERAPIST</p>
      <p class="person-quals">BSc (Psychol.), BA, Dip. (Couns. &amp; Psych.)<br>PG.Cert (CBT), FGTrK,</p>
      <ul class="contact-list">
        <li><svg viewBox="0 0 13 13"><rect x="3" y="0.5" width="7" height="12" rx="1" fill="none" stroke="#fff" stroke-width="1.4"/><rect x="5.5" y="10" width="2" height="1" fill="#fff"/></svg>555 210 4471</li>
        <li><svg viewBox="0 0 13 13"><rect x="1" y="3" width="11" height="7.5" fill="#fff"/><path d="M1 3 L6.5 7.5 L12 3" fill="none" stroke="#353535" stroke-width="1"/></svg>dara@Kindlegrove.com</li>
        <li><svg viewBox="0 0 13 13"><circle cx="6.5" cy="6.5" r="5.5" fill="#fff"/><path d="M3 4 Q5 5 4.5 7 Q6 8 5.5 10 M8 3 Q9 5 10.5 6" fill="none" stroke="#353535" stroke-width="1.2"/></svg>www.Kindlegrove.com</li>
      </ul>
    </div>
    <div class="brand-lockup">
      <span class="brand-dot"></span>
      <span class="brand-name">Kindle Grove</span>
    </div>
  </section>

  <section class="card card-back">
    <p class="back-name">Kindle Grove</p>
    <p class="tagline">Caring For Your Psychological Well-Being Is Our Top Priority</p>
  </section>
</body>
</html>
```